Heron Dusk business card design

I make handmade colourful women's beaded jewellery (necklaces and earnings).
I require a business card to be designed to truly reflect my jewellery, that is, it is different and stands out.
I would like the business card to look creative, arty, gentle and feminine and fit in with the look of my website and logo (already developed).
I would like the business card to have strong use of the water reeds that are flowing in the wind (please see the banner image on my website www.herondusk.net and attached files).

Target Market(s)

Women who are fashion conscious, hip and funky. My audience like things that are a little different and stand out in a crowd.These women are aged in their 20's-40's.

Industry/Entity Type

Jewelry

Contact Information for Business Card

Please include the following items:
1) my logo: Heron Dusk
2) my name, address and phone number: Darla Fontenot, Sydney, Australia, 0498 315 270
3) my web details: www.herondusk.net, info@herondusk.net, www.facebook.com/herondusk

Font styles to use
Other font styles liked:
• Remachine Script

Requirements
Must have
• My business card must have the following:
• 1) my personal details including all my website contacts (see above).
• 2) Heron Dusk logo
• 3) Reeds flowing in the wind (see my banner image on my website www.herondusk.net or see attached files).
Nice to have
• A sunrise in the background (rising over water)
• I would prefer that the colour scheme to fit with the Heron Dusk logo, that is the colours of an early morning sunrise i.e yellows, oranges. The use of black and white is fine.
Should not have
• I do not like a commercial manufactured look with hard edges. I would like a look that is soft and reflects an artistic, creative and independent business.

```html
<!DOCTYPE html>
<html lang="en">
<head>
<meta charset="utf-8">
<title>Heron Dusk business card</title>
<link rel="stylesheet" href="https://fonts.googleapis.com/css2?family=Open+Sans:wght@400;700&display=swap">
<style>
  :root {
    --page: #efe9e1;
    --sun-yellow: #ffd21f;
    --sun-orange: #f68b1e;
    --sun-deep: #e8621a;
    --ring-dark: #2b2b2b;
    --grey-light: #d4d4d4;
    --grey-mid: #8f8f8f;
    --ink: #111111;
    --text-yellow: #f2d21a;
    --text-soft: #e9e9e9;
    --gold-light: #d9a63a;
    --gold-dark: #5a3812;
    --white: #ffffff;
  }
  * { box-sizing: border-box; margin: 0; padding: 0; }
  html, body { width: 1200px; height: 913px; overflow: hidden; }
  body {
    background: var(--page);
    font-family: "Open Sans", Arial, sans-serif;
    position: relative;
  }
  .card {
    position: absolute;
    top: 306px;
    width: 525px;
    height: 300px;
    border-radius: 22px;
    overflow: hidden;
    box-shadow: 0 10px 28px rgba(0,0,0,.25);
  }
  .card--front { left: 50px; background: linear-gradient(160deg, var(--grey-light) 0%, var(--grey-mid) 45%, var(--ink) 85%); }
  .card--back { left: 625px; background: radial-gradient(circle at 78% 30%, #f6d27a 0%, var(--gold-light) 30%, #8a5a1e 70%, var(--gold-dark) 100%); }

  .front-reeds {
    position: absolute; left: 200px; top: 40px; right: 0; bottom: 0;
    background: linear-gradient(180deg, rgba(17,17,17,0) 0%, rgba(17,17,17,.55) 45%, var(--ink) 100%);
  }
  .front-sun { position: absolute; left: 0; top: 0; width: 300px; height: 300px; }
  .sun-scene {
    position: absolute; left: 0; top: 92px; width: 230px; height: 208px;
  }
  .contact {
    position: absolute; right: 28px; top: 34px; text-align: right; color: var(--text-yellow);
  }
  .contact__name { font-size: 25px; font-weight: 700; line-height: 1.1; }
  .contact__role { font-size: 14px; color: var(--text-soft); margin-top: 2px; }
  .contact__place { font-size: 14px; margin-top: 4px; }
  .contact__lines { margin-top: 26px; font-size: 14px; line-height: 1.6; }

  .back-reeds {
    position: absolute; inset: 0;
    background: linear-gradient(180deg, rgba(58,34,10,0) 0%, rgba(58,34,10,.5) 55%, rgba(40,22,6,.85) 100%);
  }
  .brand {
    position: absolute; left: 60px; top: 70px; display: flex; align-items: center; gap: 22px;
  }
  .brand__name { font-size: 40px; font-weight: 400; color: var(--white); }
  .brand__mark {
    width: 150px; height: 150px; border-radius: 50%;
    background: var(--sun-orange); border: 5px solid var(--white);
  }
</style>
</head>
<body>
  <section class="card card--front">
    <div class="front-reeds" role="img" aria-label="Silhouetted water reeds flowing in the wind"></div>
    <svg class="front-sun" viewBox="0 0 300 300" aria-hidden="true">
      <defs>
        <radialGradient id="sunGlow" cx="35%" cy="25%" r="80%">
          <stop offset="0" stop-color="#fff06a"/>
          <stop offset=".45" stop-color="#ffd21f"/>
          <stop offset="1" stop-color="#f68b1e"/>
        </radialGradient>
      </defs>
      <circle cx="110" cy="200" r="178" fill="none" stroke="#f68b1e" stroke-width="9"/>
      <circle cx="110" cy="200" r="165" fill="none" stroke="#2b2b2b" stroke-width="12"/>
      <circle cx="110" cy="200" r="152" fill="url(#sunGlow)"/>
    </svg>
    <div class="sun-scene" role="img" aria-label="Pelican silhouette perched on a post before a sunrise over water, with reeds"></div>
    <div class="contact">
      <p class="contact__name">Darla Fontenot</p>
      <p class="contact__role">Owner</p>
      <p class="contact__place">Sydney, Australia</p>
      <div class="contact__lines">
        <p>0498 315 270</p>
        <p>www.facebook.com/herondusk</p>
        <p>info@herondusk.net</p>
        <p>www.herondusk.net</p>
      </div>
    </div>
  </section>

  <section class="card card--back">
    <div class="back-reeds" role="img" aria-label="Cattails and reeds silhouetted against a golden sunrise"></div>
    <div class="brand">
      <span class="brand__name">Heron Dusk</span>
      <span class="brand__mark"></span>
    </div>
  </section>
</body>
</html>
```